Accounting firm needing business card / letterhead designed
Marcus L. Trenholm, CPA
marcus@veltrowledger.com
www.veltrowledger.com
842 E Alder Ave Halvern, MN 43827
555-562-0974

```html
<!DOCTYPE html>
<html lang="en">
<head>
<meta charset="utf-8">
<title>Veltrow Ledger – Business Card</title>
<link rel="stylesheet" href="https://fonts.googleapis.com/css2?family=Roboto:wght@400;500;700&family=Roboto+Condensed:wght@500&display=swap">
<style>
  :root {
    --navy: #231f5e;
    --green: #86c03f;
    --paper: #f3f3f3;
    --white: #ffffff;
    --backdrop: #e4e1dc;
  }
  * { margin: 0; padding: 0; box-sizing: border-box; }
  html, body { width: 1200px; height: 960px; overflow: hidden; }
  body {
    background: var(--backdrop);
    font-family: "Roboto", Arial, sans-serif;
    position: relative;
  }
  .card {
    position: absolute;
    width: 600px;
    height: 343px;
    box-shadow: 0 2px 6px rgba(0,0,0,0.25);
  }
  .card--front { left: 314px; top: 113px; background: var(--paper); }
  .card--back { left: 311px; top: 472px; background: var(--navy); }

  .wordmark {
    position: absolute;
    left: 0; right: 0;
    text-align: center;
    font-family: "Roboto", Arial, sans-serif;
    font-weight: 700;
    font-size: 38px;
    letter-spacing: 3px;
    line-height: 1;
  }
  .card--front .wordmark { top: 84px; color: var(--navy); }
  .card--back .wordmark { top: 140px; color: var(--white); }

  .band {
    position: absolute;
    top: 217px;
    height: 98px;
  }
  .band--identity {
    left: 0; width: 299px;
    background: var(--navy);
    color: var(--white);
    padding: 18px 0 0 34px;
  }
  .band--contact {
    left: 302px; width: 298px;
    background: var(--green);
    color: var(--white);
    padding: 24px 32px 0 0;
    text-align: right;
  }
  .holder-name {
    font-family: "Roboto Condensed", Arial, sans-serif;
    font-weight: 500;
    font-size: 20px;
    line-height: 24px;
    margin-bottom: 3px;
  }
  .address { font-size: 14.5px; line-height: 19px; }
  .contact-line {
    display: flex;
    justify-content: flex-end;
    align-items: center;
    gap: 7px;
    font-size: 14.5px;
    line-height: 19px;
  }
  .contact-line svg { width: 12px; height: 12px; fill: var(--white); flex: none; }

  .back-url {
    position: absolute;
    left: 0; right: 0; top: 283px;
    text-align: center;
    color: var(--white);
    font-size: 14px;
    letter-spacing: 6.5px;
  }
</style>
</head>
<body>
  <section class="card card--front">
    <div class="wordmark">VELTROW LEDGER</div>
    <div class="band band--identity">
      <div class="holder-name">Marcus L. Trenholm, CPA</div>
      <div class="address">842 E Alder Ave<br>Halvern, MN 43827</div>
    </div>
    <div class="band band--contact">
      <div class="contact-line">555-562-0974
        <svg viewBox="0 0 24 24" aria-hidden="true"><path d="M6.6 10.8a15.1 15.1 0 0 0 6.6 6.6l2.2-2.2a1 1 0 0 1 1-.25 11.4 11.4 0 0 0 3.6.57 1 1 0 0 1 1 1V20a1 1 0 0 1-1 1A17 17 0 0 1 3 4a1 1 0 0 1 1-1h3.5a1 1 0 0 1 1 1c0 1.25.2 2.45.57 3.57a1 1 0 0 1-.25 1z"/></svg>
      </div>
      <div class="contact-line">marcus@veltrowledger.com
        <svg viewBox="0 0 24 24" aria-hidden="true"><path d="M2 5h20l-10 7z"/><path d="M2 7l10 7 10-7v12H2z"/></svg>
      </div>
      <div class="contact-line">www.veltrowledger.com
        <svg viewBox="0 0 24 24" aria-hidden="true"><circle cx="12" cy="12" r="10"/><path d="M7 8c2 0 3 1 3 3s-2 2-2 4 1 3 1 4M15 5c-1 1-2 2-1 3s3 0 3 2-2 2-2 4 2 2 3 2" fill="none" stroke="#86c03f" stroke-width="1.6"/></svg>
      </div>
    </div>
  </section>

  <section class="card card--back">
    <div class="wordmark">VELTROW LEDGER</div>
    <div class="back-url">www.veltrowledger.com</div>
  </section>
</body>
</html>
```